Website for a Psychologist in Private Practice

I need a cool web design for my website: www.drkalvoric.com. I would like it to look professional. Keep all the current content and add: Space for video; radio spots (see Silver Cedar Tunes Logo below for those); Quick Inquiry; Friendora link; 5 star rating on Rivo; a map; reviews from former patients. I am open to suggestions.

Target Market(s)

Those seeking individual and marital counseling.

Industry/Entity Type

Mental Health

Number of Pages Required

1 page

Font styles to use
Sans Serif
Other font styles liked:
• I'm open but no hard to read script

Requirements
Must have
• All the content on my home page with link for video and radio spots. List services and degrees and expertices (pics not necessary).
Nice to have
• A video of me and radio conversations (logo of Silver Cedar Tunes radio attached).
Should not have
• Cartoons, comedy, etc.... I don't need pictures of services (marital, depression, etc...) Just list those.

```html
<!DOCTYPE html>
<html lang="en">
<head>
<meta charset="utf-8">
<title>Dr. Mara Kalvoric – Clinical Psychologist</title>
<link rel="stylesheet" href="https://fonts.googleapis.com/css2?family=Josefin+Sans:wght@300;400;600;700&family=Oswald:wght@500&family=Roboto:wght@400;500;700&display=swap">
<style>
:root{
  --gold:#c7b15b;
  --gold-dark:#8f7d28;
  --gold-deep:#a4913a;
  --blue:#2f6d9c;
  --blue-dark:#24577d;
  --blue-bright:#2e86c8;
  --navy:#1f4f7a;
  --ink:#3c3c3c;
  --muted:#7a7a7a;
  --paper:#ecebe8;
  --white:#ffffff;
  --orange:#d9501a;
  --star:#e2a623;
}
html,body{margin:0;padding:0;overflow:hidden}
body{width:1200px;height:2875px;font-family:'Roboto',sans-serif;color:var(--ink);background:var(--white)}
.page{position:relative;width:1200px;height:2875px;overflow:hidden}
.abs{position:absolute}
.backdrop{position:absolute;left:0;top:0}

/* header */
.brand{left:73px;top:24px;font-family:'Josefin Sans',sans-serif;font-size:34px;color:#555;font-weight:400}
.brand b{font-weight:400;color:#333}
.header-contact{right:73px;top:18px;text-align:right}
.header-phone{font-family:'Oswald',sans-serif;font-size:28px;color:#3a3a3a;display:flex;align-items:center;gap:10px}
.phone-dot{width:32px;height:32px;border-radius:50%;background:var(--gold);display:inline-flex;align-items:center;justify-content:center}
.header-mail{font-size:15px;color:var(--muted);margin-top:2px}

.nav{left:0;top:96px;width:1200px;height:42px;background:var(--gold)}
.nav ul{list-style:none;margin:0;padding:0 0 0 77px;display:flex;height:42px}
.nav li{font-family:'Roboto',sans-serif;font-weight:700;font-size:15px;color:var(--white);padding:0 10px;line-height:42px}
.nav li.active{background:var(--gold-dark)}
.nav-address{position:absolute;right:73px;top:0;line-height:42px;color:var(--white);font-size:14px;display:flex;align-items:center;gap:8px}

/* hero */
.hero-frame{left:73px;top:165px;width:1054px;height:529px;background:rgba(255,255,255,.35);box-sizing:border-box;padding:4px}
.hero-photo{width:100%;height:100%;background:linear-gradient(100deg,#5b4a1e 0%,#c98a2a 30%,#f0b64a 45%,#b07a2a 65%,#5a4a22 100%)}
.hero-title{left:569px;top:272px;font-family:'Josefin Sans',sans-serif;font-weight:700;font-size:35px;line-height:35px;color:var(--orange);white-space:nowrap}
.hero-arrow{top:420px;width:34px;height:34px}

.tile{top:703px;height:225px;overflow:hidden}
.tile-photo{width:100%;height:100%}
.tile-label{position:absolute;left:0;right:0;bottom:24px;font-family:'Josefin Sans',sans-serif;font-weight:600;font-size:22px;color:var(--white);text-align:center}
.tile-label.left{text-align:left;padding-left:28px}
.radio-title{position:absolute;top:24px;left:0;right:0;text-align:center;font-family:'Josefin Sans',sans-serif;font-weight:600;font-size:22px;color:var(--white)}
.radio-band{position:absolute;left:14px;right:14px;top:162px;height:36px;background:#e0305d;display:flex;align-items:center;justify-content:center;font-family:'Josefin Sans',sans-serif;font-weight:700;font-size:24px;color:#2a2a2a}

/* welcome */
.welcome{left:73px;top:1040px;width:665px;color:var(--white)}
.welcome-kicker{font-family:'Josefin Sans',sans-serif;font-size:26px;font-weight:300;line-height:28px}
.welcome-name{font-family:'Josefin Sans',sans-serif;font-size:38px;font-weight:400;line-height:40px;margin-bottom:10px}
.welcome p{font-size:14px;line-height:24px;margin:0 0 14px}

.inquiry{left:792px;top:1010px;width:335px;height:548px;background:var(--gold);box-sizing:border-box;padding:40px 21px 0;text-align:center}
.inquiry-kicker{font-family:'Roboto',sans-serif;font-weight:500;font-size:16px;color:var(--white)}
.inquiry-pill{margin:4px auto 0;height:34px;line-height:36px;border-radius:17px;background:var(--blue-bright);color:var(--white);font-family:'Roboto',sans-serif;font-weight:500;font-size:22px}
.inquiry-note{font-size:13px;color:var(--white);line-height:18px;margin:10px 0 14px}
.field{background:var(--white);border-radius:5px;height:38px;box-sizing:border-box;padding:0 10px;text-align:left;font-size:13px;color:#666;line-height:38px;margin-bottom:10px}
.field.area{height:166px;line-height:22px;padding-top:8px}
.submit{height:39px;border-radius:4px;background:var(--navy);color:var(--white);font-weight:700;font-size:15px;line-height:39px;margin-top:14px}

/* reviews */
.reviews-ribbon{left:428px;top:1698px;width:344px;height:46px;border-radius:23px;background:var(--gold);color:var(--white);font-family:'Josefin Sans',sans-serif;font-weight:600;font-size:23px;text-align:center;line-height:50px;z-index:2}
.quote-mark{font-family:'Josefin Sans',sans-serif;font-size:64px;color:var(--gold);line-height:1;z-index:1}
.review{top:1796px;width:334px;height:236px;background:rgba(240,236,228,.88);border-radius:6px;box-sizing:border-box;padding:26px 26px 0}
.review p{margin:0;text-align:center;font-size:14px;line-height:27px;color:#6a6a6a}
.review-open{position:absolute;left:14px;top:-10px;font-family:'Josefin Sans',sans-serif;font-size:60px;color:#cfc7b4;line-height:1}
.review-close{position:absolute;right:14px;top:164px;font-family:'Josefin Sans',sans-serif;font-size:60px;color:#cfc7b4;line-height:1}
.review-author{position:absolute;left:16px;bottom:12px;display:flex;align-items:center;gap:12px}
.avatar{width:54px;height:54px;border-radius:50%;background:linear-gradient(#8a6a4e,#c9a682);border:3px solid var(--gold)}
.author-name{font-family:'Josefin Sans',sans-serif;font-weight:600;font-size:18px;color:#333}
.author-role{font-size:13px;color:var(--muted)}
.stars{position:absolute;right:18px;bottom:20px;font-size:16px;color:var(--star);letter-spacing:1px}
.stars span{color:#bbb}

/* expertise */
.expertise{left:60px;top:2282px;width:540px;text-align:center;font-family:'Josefin Sans',sans-serif}
.expertise h3{margin:0;font-weight:400;font-size:24px;color:var(--blue-bright);letter-spacing:.5px}
.expertise .wave{color:var(--gold);font-size:16px;letter-spacing:-1px}
.expertise .row{font-size:15px;color:#777;line-height:26px}
.expertise .group{font-size:20px;color:#777;letter-spacing:.5px;line-height:26px}
.dot{color:var(--gold);padding:0 6px}
.divider{left:600px;top:2270px;width:1px;height:140px;background:#cfccc5}
.donate{left:620px;top:2285px;width:560px;text-align:center;font-family:'Josefin Sans',sans-serif;font-size:22px;color:#555}

/* footer */
.footer-col{top:2575px;color:var(--white)}
.footer-col h4{margin:0;font-size:13.5px;font-weight:700;letter-spacing:.3px}
.footer-col .sub{font-size:13px;margin-top:2px}
.footer-rule{height:1px;background:rgba(255,255,255,.35);margin:10px 0 12px}
.footer-col ul{list-style:none;margin:0;padding:0;font-size:13.5px;line-height:24px}
.contact-item{display:flex;gap:16px;align-items:flex-start;font-size:14px;line-height:20px;margin-bottom:20px}
.map{width:244px;height:158px;background:linear-gradient(135deg,#e8e3d8,#d5d2ca 60%,#c9d3c4)}
.bottom-bar{left:0;top:2818px;width:1200px;height:57px;background:var(--gold);color:var(--white);font-size:13.5px}
.bottom-bar .copy{position:absolute;left:73px;top:0;line-height:57px}
.social{position:absolute;right:73px;top:0;line-height:57px;display:flex;gap:22px}
.social span{display:flex;align-items:center;gap:7px}
.social i{display:inline-block;width:14px;height:14px;border-radius:50%;background:var(--white)}
</style>
</head>
<body>
<div class="page">

<svg class="backdrop" width="1200" height="2875" viewBox="0 0 1200 2875" aria-hidden="true">
  <defs>
    <linearGradient id="goldBand" x1="0" y1="0" x2="0" y2="1">
      <stop offset="0" stop-color="#8f7d28"/><stop offset="1" stop-color="#c7b15b"/>
    </linearGradient>
    <linearGradient id="blueBand" x1="0" y1="0" x2="1" y2="0">
      <stop offset="0" stop-color="#2a5f89"/><stop offset="1" stop-color="#3a7aa8"/>
    </linearGradient>
    <linearGradient id="footerBand" x1="0" y1="0" x2="1" y2="0">
      <stop offset="0" stop-color="#2d5a80"/><stop offset="1" stop-color="#3c6a8e"/>
    </linearGradient>
  </defs>
  <rect x="0" y="138" width="1200" height="460" fill="url(#goldBand)"/>
  <polygon points="0,968 1200,1030 1200,1560 0,1610" fill="url(#blueBand)"/>
  <polygon points="0,2225 1200,2135 1200,2490 0,2475" fill="#ecebe8"/>
  <polygon points="0,2475 1200,2490 1200,2818 0,2818" fill="url(#footerBand)"/>
  <polygon points="770,1010 792,1010 792,1575" fill="#7a6a1f"/>
</svg>

<div class="abs" role="img" aria-label="Beach photograph: turquoise shallow water over pale sand" style="left:0;top:1560px;width:1200px;height:670px;background:linear-gradient(180deg,#2f8fa0 0%,#6cc0c4 25%,#b9dcd6 42%,#d8cbb0 55%,#cbb79a 100%);clip-path:polygon(0 50px,1200px 0,1200px 580px,0 670px)"></div>

<!-- header -->
<div class="abs brand">Dr. <b>Mara Kalvoric</b></div>
<div class="abs header-contact">
  <div class="header-phone">
    <span class="phone-dot"><svg width="16" height="16" viewBox="0 0 24 24"><path fill="#fff" d="M6.6 10.8a15 15 0 006.6 6.6l2.2-2.2c.3-.3.7-.4 1-.2 1.1.4 2.3.6 3.6.6.6 0 1 .4 1 1V20c0 .6-.4 1-1 1A17 17 0 013 4c0-.6.4-1 1-1h3.5c.6 0 1 .4 1 1 0 1.3.2 2.5.6 3.6.1.3 0 .7-.2 1z"/></svg></span>
    (555) 014 2837
  </div>
  <div class="header-mail">mk@drkalvoric.com</div>
</div>

<nav class="abs nav">
  <ul>
    <li class="active">HOME</li><li>SESSIONS</li><li>RESOURCES</li><li>BIO</li><li>CONTACT</li>
  </ul>
  <div class="nav-address">
    <svg width="12" height="16" viewBox="0 0 12 16"><path fill="#fff" d="M6 0a6 6 0 00-6 6c0 4.5 6 10 6 10s6-5.5 6-10a6 6 0 00-6-6zm0 8.5A2.5 2.5 0 116 3.5a2.5 2.5 0 010 5z"/></svg>
    418 Larkspur Lane #210, Bayview, CA. 90000
  </div>
</nav>

<!-- hero -->
<div class="abs hero-frame"><div class="hero-photo" role="img" aria-label="Woman with open arms in a sunlit golden meadow at sunset"></div></div>
<div class="abs hero-title">LOREM IPSUM<br>DOLOR SIT AMET,<br>CONSECTETUR</div>
<svg class="abs hero-arrow" style="left:102px" viewBox="0 0 34 34" aria-hidden="true"><circle cx="17" cy="17" r="15" fill="rgba(255,255,255,.25)" stroke="#fff" stroke-width="2"/><path d="M20 10l-7 7 7 7" fill="none" stroke="#fff" stroke-width="3"/></svg>
<svg class="abs hero-arrow" style="left:1062px" viewBox="0 0 34 34" aria-hidden="true"><circle cx="17" cy="17" r="15" fill="rgba(255,255,255,.25)" stroke="#fff" stroke-width="2"/><path d="M14 10l7 7-7 7" fill="none" stroke="#fff" stroke-width="3"/></svg>

<div class="abs tile" style="left:73px;width:339px">
  <div class="tile-photo" role="img" aria-label="Portrait of Dr. Mara K" style="background:linear-gradient(135deg,#3f6a3a,#c9b18e 50%,#2f5a33)"></div>
  <div class="tile-label left">DR. MARA K</div>
</div>
<div class="abs tile" style="left:427px;width:346px">
  <div class="tile-photo" role="img" aria-label="Video still of a counseling session" style="background:linear-gradient(135deg,#6f6458,#a99b8a 50%,#5b5f63)"></div>
  <svg class="abs" style="left:138px;top:74px" width="70" height="70" viewBox="0 0 70 70" aria-hidden="true"><circle cx="35" cy="35" r="32" fill="rgba(255,255,255,.2)" stroke="#fff" stroke-width="4"/><path d="M28 22l20 13-20 13z" fill="#fff"/></svg>
  <div class="tile-label">WATCH OUR VIDEO</div>
</div>
<div class="abs tile" style="left:780px;width:345px;background:#6ecfcf">
  <div class="radio-title">RADIO SPOTS</div>
  <div class="abs" role="img" aria-label="Vintage wooden radio" style="left:98px;top:62px;width:148px;height:100px;border-radius:10px;background:linear-gradient(#8a5a30,#5a3518)"></div>
  <div class="radio-band">SILVER CEDAR TUNES</div>
</div>

<!-- welcome -->
<section class="abs welcome">
  <div class="welcome-kicker">Welcome to</div>
  <div class="welcome-name">DR. MARA KALVORIC</div>
  <p>I'm so glad you are here. Choosing to see a professional for issues in your life can be difficult but also possibly life changing. Many postpone seeking help because they believe doing so acknowledges failure on their part. Really? We seek the help of experts all the time (contractors, mechanics, chefs, etc...) and what is more important than your life? Consulting with a neutral party to act in your best interest can be time well spent. So if you are willing to take the time to invest in counseling, make sure that it is with someone that is worth your time.</p>
  <p>Choose a licensed psychologist with a doctoral degree (Ph.D. or PsyD.) - both have over 10 years of education in the field of psychology, extensive internships and comprehensive licensing exams. Others have far less education if any. Also, consider the therapist's approach to therapy. I use a straightforward approach (psychobabble available upon request) with brief, solution-oriented sessions.</p>
  <p>Experience also separates good psychologists from others with fewer and more proficient sessions. My 20+ years of professional experience and my life experience contributes to the empathetic perspective I use to relate to each person I see. I also believe it is the reason 90% of my practice is referral based and why many other psychologists in the area seek my services.</p>
  <p><b>DO NOT COMPROMISE.</b> Find an educated, licensed, experienced professional that you can relate to. Think about what it took to get you here and the importance resolving this issue can have on your life.</p>
</section>

<aside class="abs inquiry">
  <div class="inquiry-kicker">CONTACT US TODAY FOR YOUR</div>
  <div class="inquiry-pill">QUICK INQUIRY</div>
  <div class="inquiry-note">Fill out the form below and we'll be in touch<br>within 24 hours!</div>
  <div class="field">Name</div>
  <div class="field">Email</div>
  <div class="field">Phone</div>
  <div class="field area">How Can we help you?</div>
  <div class="submit">SUBMIT</div>
</aside>

<!-- reviews -->
<div class="abs quote-mark" style="left:444px;top:1672px">&ldquo;</div>
<div class="abs reviews-ribbon">REVIEWS FROM PATIENTS</div>
<div class="abs quote-mark" style="left:722px;top:1742px">&rdquo;</div>

<div class="abs review" style="left:73px">
  <div class="review-open">&ldquo;</div>
  <p>Lorem ipsum dolor sit amet, consectetur adipiscing elit, sed do eiusmod tempor incididunt ut labore et dolore magna aliqua. Ut enim ad minim veniam, quis nostrud.</p>
  <div class="review-close">&rdquo;</div>
  <div class="review-author"><div class="avatar" role="img" aria-label="Patient photo"></div><div><div class="author-name">John Doe</div><div class="author-role">Lorem Ipsum</div></div></div>
  <div class="stars">★★★★<span>★</span></div>
</div>
<div class="abs review" style="left:433px">
  <div class="review-open">&ldquo;</div>
  <p>Lorem ipsum dolor sit amet, consectetur adipiscing elit, sed do eiusmod tempor incididunt ut labore et dolore magna aliqua. Ut enim ad minim veniam, quis nostrud.</p>
  <div class="review-close">&rdquo;</div>
  <div class="review-author"><div class="avatar" role="img" aria-label="Patient photo"></div><div><div class="author-name">John Doe</div><div class="author-role">Lorem Ipsum</div></div></div>
  <div class="stars">★★★★<span>★</span></div>
</div>
<div class="abs review" style="left:793px">
  <div class="review-open">&ldquo;</div>
  <p>Lorem ipsum dolor sit amet, consectetur adipiscing elit, sed do eiusmod tempor incididunt ut labore et dolore magna aliqua. Ut enim ad minim veniam, quis nostrud.</p>
  <div class="review-close">&rdquo;</div>
  <div class="review-author"><div class="avatar" role="img" aria-label="Patient photo"></div><div><div class="author-name">John Doe</div><div class="author-role">Lorem Ipsum</div></div></div>
  <div class="stars">★★★★<span>★</span></div>
</div>

<svg class="abs" style="left:73px;top:2052px" width="1054" height="24" viewBox="0 0 1054 24" aria-hidden="true">
  <line x1="0" y1="12" x2="490" y2="12" stroke="#fff" stroke-width="1.5"/>
  <line x1="564" y1="12" x2="1054" y2="12" stroke="#fff" stroke-width="1.5"/>
  <line x1="520" y1="12" x2="534" y2="12" stroke="#fff" stroke-width="1.5"/>
  <circle cx="503" cy="12" r="10" fill="none" stroke="#fff" stroke-width="1.5"/><path d="M506 7l-5 5 5 5" fill="none" stroke="#fff" stroke-width="1.5"/>
  <circle cx="551" cy="12" r="10" fill="none" stroke="#fff" stroke-width="1.5"/><path d="M548 7l5 5-5 5" fill="none" stroke="#fff" stroke-width="1.5"/>
</svg>

<!-- expertise -->
<section class="abs expertise">
  <h3><span class="wave">〰〰〰</span> EXPERTISE <span class="wave">〰〰〰</span></h3>
  <div class="row">Dating<span class="dot">•</span>Marriage<span class="dot">•</span>Parenting &amp; Professional</div>
  <div class="group">RELATIONSHIPS</div>
  <div class="row">Depression &amp; Anxiety Issues<span class="dot">•</span>Personality Disorders<span class="dot">•</span>Life Management</div>
</section>
<div class="abs divider"></div>
<div class="abs donate">A portion of all revenue is donated to</div>
<div class="abs" style="left:660px;top:2330px;width:58px;height:58px;border-radius:50%;background:#d8363c"></div>
<div class="abs" style="left:890px;top:2335px;width:120px;height:50px;border-radius:6px;background:#8e9a3a"></div>

<!-- footer -->
<div class="abs footer-col" style="left:73px;width:240px">
  <h4>CLINICAL PSYCHOLOGIST</h4>
  <div class="sub">California # PSY20581</div>
  <div class="footer-rule"></div>
  <ul>
    <li>Doctoral Degree in Clinical Psychology</li>
    <li>Masters Degree in Counseling</li>
    <li>Psychology Doctoral Internship, Coastal</li>
    <li>University Medical Center Internship,</li>
    <li>Harbor Clinic</li>
  </ul>
</div>
<div class="abs footer-col" style="left:345px;width:240px">
  <h4>CONTACT INFORMATION</h4>
  <div class="footer-rule"></div>
  <div class="contact-item"><svg width="16" height="20" viewBox="0 0 12 16"><path fill="#fff" d="M6 0a6 6 0 00-6 6c0 4.5 6 10 6 10s6-5.5 6-10a6 6 0 00-6-6zm0 8.5A2.5 2.5 0 116 3.5a2.5 2.5 0 010 5z"/></svg><span>418 Larkspur Lane, Suite 210<br>Bayview, CA 90000</span></div>
  <div class="contact-item" style="font-size:17px"><svg width="18" height="18" viewBox="0 0 24 24"><path fill="#fff" d="M6.6 10.8a15 15 0 006.6 6.6l2.2-2.2c.3-.3.7-.4 1-.2 1.1.4 2.3.6 3.6.6.6 0 1 .4 1 1V20c0 .6-.4 1-1 1A17 17 0 013 4c0-.6.4-1 1-1h3.5c.6 0 1 .4 1 1 0 1.3.2 2.5.6 3.6.1.3 0 .7-.2 1z"/></svg><span>(555) 014 2837</span></div>
  <div class="contact-item"><svg width="20" height="16" viewBox="0 0 20 14"><rect x="0" y="0" width="20" height="14" rx="1" fill="#fff"/><path d="M0 0l10 8 10-8" fill="none" stroke="#2d5a80" stroke-width="1.5"/></svg><span>mk@drkalvoric.com</span></div>
</div>
<div class="abs footer-col" style="left:613px;width:244px">
  <h4>FIND US ON MAP</h4>
  <div class="footer-rule"></div>
  <div class="map" role="img" aria-label="Street map showing the office location"></div>
</div>
<div class="abs footer-col" style="left:882px;width:245px">
  <h4>QUICK LINKS</h4>
  <div class="footer-rule"></div>
  <ul><li>Home</li><li>Sessions</li><li>Resources</li><li>Bio</li><li>Contact</li></ul>
</div>

<div class="abs bottom-bar">
  <div class="copy">©2016 Dr. Mara Kalvoric. All Rights Reserved.</div>
  <div class="social"><span><i></i>Rivo</span><span><i></i>Friendora</span><span><i></i>Chirply</span></div>
</div>

</div>
</body>
</html>
```